Qvx Brightforge Website

All the descriptions are available in the attached file. The designer has to structure the website and find the right images and icons. The website should look modern and avoid using images of real humans rather use animated images. Please note that the design should include home page, all the 4 services page , the contact us would be at the bottom of home page.

```html
<!DOCTYPE html>
<html lang="en">
<head>
<meta charset="utf-8">
<title>Qvx Brightforge – IT Consulting</title>
<link rel="stylesheet" href="https://fonts.googleapis.com/css2?family=Audiowide&family=Nunito+Sans:wght@400;600;700&family=Roboto:wght@500;700&display=swap">
<style>
:root{
  --blue:#0a6fdc;
  --blue-bright:#1477e6;
  --orange:#ffa108;
  --ink:#2b2b2b;
  --text:#3a3a3a;
  --line:#d4d8de;
  --grey-band:#f4f5f7;
  --hero-top:#eef0f3;
  --hero-tint:#dbe8f7;
  --white:#ffffff;
}
*{box-sizing:border-box;margin:0;padding:0}
html,body{width:1200px;height:3701px;overflow:hidden}
body{position:relative;background:var(--white);font-family:"Nunito Sans",sans-serif;color:var(--text)}
.abs{position:absolute}
.display{font-family:"Audiowide",sans-serif;color:var(--blue);font-weight:400}
.btn{position:absolute;display:flex;align-items:center;justify-content:center;background:var(--orange);color:var(--white);border-radius:22px;font-size:17px;font-weight:600}

/* header */
.brand{left:115px;top:28px;width:140px;font-family:"Audiowide",sans-serif;color:var(--blue);font-size:21px;line-height:25px}
.nav{left:587px;top:51px;display:flex;font-size:15px;color:var(--ink)}
.nav span{margin-right:45px}

/* hero */
.hero-bg{left:0;top:0;width:1200px;height:760px;background:linear-gradient(180deg,var(--hero-top) 0%,var(--white) 100%)}
.hero-art{left:0;top:330px;width:1200px;height:410px;background:linear-gradient(180deg,rgba(219,232,247,0) 0%,var(--hero-tint) 55%,rgba(219,232,247,.35) 100%)}
.hero-title{left:0;width:1200px;top:222px;text-align:center;font-size:50px}
.hero-sub{left:0;width:1200px;top:288px;text-align:center;font-family:"Audiowide",sans-serif;font-size:22px;line-height:33px;color:#111}
.hero-copy{left:0;width:1200px;top:366px;text-align:center;font-size:17px;line-height:29px}

/* about */
.about-title{left:600px;top:836px;font-size:36px}
.about-copy{left:602px;top:902px;width:488px;font-size:17px;line-height:29.3px;text-align:justify}

/* offer */
.offer-band{left:0;top:1255px;width:1200px;height:910px}
.offer-title{left:0;width:1200px;top:1372px;text-align:center;font-size:38px}
.offer-copy{left:0;width:1200px;top:1443px;text-align:center;font-size:16.5px;line-height:30px;letter-spacing:-.4px}
.card{position:absolute;top:1538px;width:306px;height:477px;background:var(--white);border:1px solid var(--line);border-radius:10px;overflow:hidden}
.card-head{height:183px;background:var(--blue);position:relative}
.card-icon{position:absolute;left:23px;top:24px}
.card-title{position:absolute;left:22px;bottom:14px;font-family:"Roboto",sans-serif;font-weight:700;color:var(--white);font-size:30px;line-height:31px;white-space:nowrap}
.card-copy{padding:22px 18px 0;text-align:center;font-size:17px;line-height:27.4px}
.card .btn{left:81px;top:413px;width:143px;height:42px}

/* products */
.prod-title{left:112px;top:2256px;font-size:36px}
.prod-copy{left:115px;top:2313px;width:487px;font-size:17px;line-height:29.3px;text-align:justify}

/* contact */
.contact-band{left:0;top:2730px;width:1200px;height:607px;background:var(--grey-band)}
.contact-title{left:115px;top:2810px;font-size:36px}
.contact-copy{left:115px;top:2873px;font-size:18px;line-height:31px;color:var(--ink)}
.social{position:absolute;width:34px;height:34px;border-radius:50%}
.field{position:absolute;left:601px;width:478px;height:64px;background:var(--white);border:1px solid #b9bec6;font-size:19px;color:#8a8f96;padding:19px 31px}

/* footer */
.footer{left:0;top:3337px;width:1200px;height:364px;background:var(--blue)}
.f-brand{left:117px;top:3418px;width:160px;font-family:"Audiowide",sans-serif;color:var(--white);font-size:24px;line-height:30px}
.f-head{top:3412px;font-family:"Roboto",sans-serif;font-weight:500;font-size:17px;color:var(--white)}
.f-list{top:3463px;font-size:14px;line-height:26px;color:#e8f1fc}
.f-icons{left:685px;top:3468px;width:14px}
.f-rule{height:1px;background:rgba(255,255,255,.45)}
.copyright{left:0;width:1200px;top:3660px;text-align:center;font-size:15px;color:#e8f1fc}
</style>
</head>
<body>

<!-- HERO -->
<div class="abs hero-bg"></div>
<div class="abs hero-art" role="img" aria-label="Soft blue abstract mesh wave behind the hero headline"></div>

<div class="abs brand">Qvx<br>Brightforge</div>
<nav class="abs nav"><span>HOME</span><span>SERVICES</span><span>PRODUCTS</span><span>BLOG</span><span>CONTACT US</span></nav>

<h1 class="abs display hero-title">QVX BRIGHTFORGE</h1>
<p class="abs hero-sub">ADVANCING INNOVATION THROUGH IT<br>CONSULTING</p>
<p class="abs hero-copy">Empower your digital journey with our advanced IT solutions. From<br>data to web and mobile apps, we've got you covered.</p>
<div class="btn" style="left:522px;top:449px;width:156px;height:43px">Get Started</div>

<!-- ABOUT -->
<svg class="abs" style="left:0;top:781px" width="526" height="414" viewBox="0 0 526 414">
  <defs>
    <linearGradient id="aboutFill" x1="0" y1="0" x2="1" y2="1">
      <stop offset="0" stop-color="#3a1c8c"/><stop offset=".6" stop-color="#4b26a8"/><stop offset="1" stop-color="#2a1170"/>
    </linearGradient>
  </defs>
  <path d="M0 0 H498 Q526 0 526 28 V386 Q526 414 498 414 H230 Q60 404 0 270 Z" fill="url(#aboutFill)" role="img" aria-label="Illustration of a computer screen with code and data panels"/>
  <path d="M0 270 Q60 404 230 414" fill="none" stroke="var(--blue-bright)" stroke-width="6"/>
</svg>
<h2 class="abs display about-title">ABOUT US</h2>
<p class="abs about-copy">We are a forward-thinking IT consulting firm specializing in providing cutting-edge data analytics, web application development, and mobile app development services. Our passion for innovation and technology drives us to deliver tailor-made solutions that empower businesses to thrive in the digital landscape.</p>
<div class="btn" style="left:600px;top:1100px;width:142px;height:42px">Read More</div>

<!-- WE OFFER -->
<svg class="abs offer-band" viewBox="0 0 1200 910" aria-hidden="true">
  <path d="M0 0 L1200 70 V910 L0 815 Z" fill="var(--grey-band)"/>
</svg>
<h2 class="abs display offer-title">WE OFFER</h2>
<p class="abs offer-copy">Empower your digital journey with our advanced IT solutions. From data to web and mobile apps, we've<br>got you covered.</p>

<div class="card" style="left:112px">
  <div class="card-head">
    <svg class="card-icon" width="68" height="68" viewBox="0 0 68 68" fill="none" stroke="#fff" stroke-width="2"><rect x="2" y="14" width="60" height="40" rx="3"/><path d="M10 44 L24 32 L34 38 L52 22"/><line x1="22" y1="62" x2="42" y2="62"/></svg>
    <div class="card-title">Data Analytics</div>
  </div>
  <p class="card-copy">At Qvx Brightforge, our proficiency consists of linking your leadership team's objectives with the relevant data that holds significance.</p>
  <div class="btn">Learn More</div>
</div>
<div class="card" style="left:441px">
  <div class="card-head">
    <svg class="card-icon" width="68" height="68" viewBox="0 0 68 68" fill="none" stroke="#fff" stroke-width="2"><rect x="2" y="4" width="56" height="40" rx="4"/><line x1="2" y1="16" x2="58" y2="16"/><path d="M18 26 L12 31 L18 36 M30 26 L36 31 L30 36"/><circle cx="52" cy="52" r="9"/></svg>
    <div class="card-title">Web Development</div>
  </div>
  <p class="card-copy">At Qvx Brightforge, we are a trailblazing web development company committed to delivering cutting-edge digital solutions that empower businesses to excel in the ever-evolving online landscape.</p>
  <div class="btn">Learn More</div>
</div>
<div class="card" style="left:769px">
  <div class="card-head">
    <svg class="card-icon" width="68" height="68" viewBox="0 0 68 68" fill="none" stroke="#fff" stroke-width="2"><rect x="18" y="2" width="28" height="56" rx="4"/><line x1="28" y1="52" x2="36" y2="52"/><path d="M28 24 L23 29 L28 34 M36 24 L41 29 L36 34"/></svg>
    <div class="card-title">Mobile App<br>Development</div>
  </div>
  <p class="card-copy">At Qvx Brightforge, we are a pioneering mobile app development company dedicated to crafting exceptional digital experiences that captivate and engage users across various platforms.</p>
  <div class="btn">Learn More</div>
</div>
<div class="card" style="left:1097px">
  <div class="card-head">
    <svg class="card-icon" width="68" height="68" viewBox="0 0 68 68" fill="none" stroke="#fff" stroke-width="2"><path d="M34 4 Q44 16 44 36 H24 Q24 16 34 4 Z"/><path d="M24 30 L16 44 H24 M44 30 L52 44 H44"/><path d="M30 48 V58 M38 48 V58"/></svg>
    <div class="card-title">Start-up<br>Tech Partner</div>
  </div>
  <p class="card-copy">At Qvx Brightforge, our commitment to early-stage founders guides their journey to growth with comprehensive support.</p>
  <div class="btn">Learn More</div>
</div>

<!-- PRODUCTS -->
<h2 class="abs display prod-title">PRODUCTS</h2>
<p class="abs prod-copy">Lorem ipsum dolor sit amet, consectetur adipiscing elit, sed do eiusmod tempor incididunt ut labore et dolore magna aliqua. Quis ipsum suspendisse ultrices gravida. Risus commodo viverra maecenas accumsan lacus vel facilisis. Quis ipsum suspendisse ultrices gravida. Risus commodo viverra maecenas accumsan lacus vel facilisis.</p>
<div class="btn" style="left:115px;top:2522px;width:143px;height:42px">Learn More</div>
<svg class="abs" style="left:661px;top:2225px" width="539" height="413" viewBox="0 0 539 413">
  <defs>
    <linearGradient id="prodFill" x1="0" y1="0" x2="1" y2="1">
      <stop offset="0" stop-color="#f2f2f2"/><stop offset=".55" stop-color="#d6d6d6"/><stop offset="1" stop-color="#9a9a9a"/>
    </linearGradient>
  </defs>
  <path d="M30 0 H539 V413 H240 Q40 390 8 160 Q2 60 12 20 Q16 0 30 0 Z" fill="url(#prodFill)" role="img" aria-label="Open hand beneath floating technology and communication icons"/>
  <path d="M30 0 Q16 0 12 20 Q2 60 8 160 Q40 390 240 413" fill="none" stroke="var(--blue-bright)" stroke-width="7"/>
</svg>

<!-- CONTACT -->
<div class="abs contact-band"></div>
<h2 class="abs display contact-title">CONTACT US</h2>
<p class="abs contact-copy">Address: Suite 12/40 Harlow Road,<br>Fernbury WA 6990<br>Phone: +61 (08) 5550 1234 (Sales / Support)<br>Email: hello@qvxbrightforge.example</p>
<span class="social" style="left:113px;top:3026px;background:#1da1f2" aria-label="Social link"></span>
<span class="social" style="left:158px;top:3026px;background:#e62117" aria-label="Social link"></span>
<span class="social" style="left:203px;top:3026px;background:#3b5998" aria-label="Social link"></span>
<span class="social" style="left:247px;top:3026px;background:#d6249f" aria-label="Social link"></span>
<span class="social" style="left:291px;top:3026px;background:#0a66c2" aria-label="Social link"></span>

<div class="field" style="top:2805px">First Name</div>
<div class="field" style="top:2885px">Last Name</div>
<div class="field" style="top:2965px">Email</div>
<div class="field" style="top:3045px">Phone Number</div>
<div class="field" style="top:3125px">Message</div>
<div class="btn" style="left:600px;top:3219px;width:143px;height:43px">Submit</div>

<!-- FOOTER -->
<div class="abs footer"></div>
<div class="abs f-brand">Qvx<br>Brightforge</div>

<div class="abs f-head" style="left:365px">QUICK LINKS</div>
<div class="abs f-head" style="left:522px">HELP LINKS</div>
<div class="abs f-head" style="left:707px">CONTACT</div>
<div class="abs f-head" style="left:945px">GET CONNECTED</div>
<div class="abs f-rule" style="left:350px;top:3447px;width:735px"></div>

<div class="abs f-list" style="left:367px">Home<br>Services<br>Products<br>Blog<br>Contact</div>
<div class="abs f-list" style="left:522px">Support<br>FAQ<br>Terms<br>Privacy Policy</div>
<svg class="abs f-icons" width="14" height="104" viewBox="0 0 14 104" fill="#fff" aria-hidden="true">
  <path d="M7 1 C3.8 1 1.8 3.4 1.8 6.2 C1.8 9.8 7 14 7 14 C7 14 12.2 9.8 12.2 6.2 C12.2 3.4 10.2 1 7 1 Z M7 8 A1.9 1.9 0 1 1 7 4.2 A1.9 1.9 0 1 1 7 8 Z"/>
  <path d="M2.5 54 C2.5 59 6.5 63 11.5 63 L12 60 L9.5 58.8 L8.2 60 C6.8 59.2 5.6 58 4.8 56.6 L6 55.3 L4.8 52.8 Z"/>
  <rect x="1.5" y="82" width="11" height="8" rx="1" fill="none" stroke="#fff" stroke-width="1.4"/>
  <path d="M1.8 83 L7 87 L12.2 83" fill="none" stroke="#fff" stroke-width="1.2"/>
</svg>
<div class="abs f-list" style="left:707px">Suite 12/40 Harlow Road,<br>Fernbury WA 6990<br>+61 (08) 5550 1234<br>hello@qvxbrightforge.example</div>
<span class="social" style="left:950px;top:3468px;background:#1da1f2" aria-label="Social link"></span>
<span class="social" style="left:997px;top:3468px;background:#3b5998" aria-label="Social link"></span>
<span class="social" style="left:1046px;top:3468px;background:#d6249f" aria-label="Social link"></span>

<div class="abs f-rule" style="left:107px;top:3629px;width:986px"></div>
<p class="abs copyright">© Copyrights 2023 Qvx Brightforge | All Rights Reserved</p>

</body>
</html>
```